Private Investment Firm Needs PowerPoint Presentation Template

Design PowerPoint template, take Pinebrook-submitted rough presentation draft, and drop it into new template. See attached Project Brief file for more detail.
Updates

Some decent designs have been submitted but they seem to lack the understanding of our target markets. I am hopeful that more time and feedback will result in better results.

Target Market(s)

Private company owners and intermediaries.

Font styles to use
Serif

Colors
3176b5

Requirements
Must have
• See attached Project Brief.
Nice to have
Should not have
• No B2C fluff--this is a B2B project.

```html
<!DOCTYPE html>
<html lang="en">
<head>
<meta charset="utf-8">
<title>Pinebrook Capital – Presentation Template</title>
<link rel="stylesheet" href="https://fonts.googleapis.com/css2?family=Cinzel:wght@400;500&family=Montserrat:wght@400;500;600;700&display=swap">
<style>
  :root {
    --brand-blue: #1f73bd;
    --brand-blue-light: #2a8ad6;
    --ink: #2b2b2e;
    --ink-soft: #55585c;
    --strip-grey: #6d6f72;
    --page: #e4e4e4;
    --slide: #ffffff;
  }
  * { margin: 0; padding: 0; box-sizing: border-box; }
  html, body { width: 1200px; height: 1160px; overflow: hidden; background: var(--page); }
  body { position: relative; font-family: "Montserrat", Arial, sans-serif; color: var(--ink); }

  .slide {
    position: absolute; left: 181px; width: 879px; height: 493px;
    background: var(--slide); overflow: hidden;
    box-shadow: 0 3px 10px rgba(0,0,0,.25);
  }
  .slide--title { top: 64px; }
  .slide--content { top: 586px; }
  .slide-shapes { position: absolute; inset: 0; }

  .brand { position: absolute; display: flex; align-items: center; gap: 12px; }
  .brand-dot { width: 40px; height: 40px; border-radius: 50%; background: var(--brand-blue); flex: none; }
  .brand-name {
    font-family: "Montserrat", Arial, sans-serif; font-weight: 600;
    color: var(--ink); font-size: 24px; line-height: 1; white-space: nowrap;
  }

  .slide--title .brand { left: 84px; top: 62px; }
  .slide--content .brand { left: 292px; top: 50px; }

  .deck-title {
    position: absolute; left: 41px; top: 205px;
    font-family: "Cinzel", Georgia, serif; font-weight: 500;
    font-size: 26px; line-height: 31px; color: var(--brand-blue);
  }
  .deck-subtitle {
    position: absolute; left: 41px; top: 283px; width: 300px;
    font-size: 12.5px; line-height: 18px; color: var(--ink-soft); letter-spacing: .3px;
  }
  .deck-subtitle strong { color: var(--brand-blue); font-weight: 700; }

  .photo-area { position: absolute; inset: 0; }

  .url-bar {
    position: absolute; height: 27px; background: var(--brand-blue);
    color: #fff; font-size: 13.5px; line-height: 27px; padding-left: 41px;
  }
  .url-bar strong { font-weight: 700; }
  .slide--title .url-bar { left: 0; top: 438px; width: 250px; }
  .slide--content .url-bar { left: 0; top: 452px; width: 285px; padding-left: 70px; }
  .url-slash { position: absolute; }

  .section-heading {
    position: absolute; left: 69px; top: 135px;
    font-size: 28px; font-weight: 700; color: var(--brand-blue);
  }
  .section-rule { position: absolute; left: 69px; top: 172px; width: 62px; height: 4px; background: var(--brand-blue); border-radius: 2px; }

  .points {
    position: absolute; left: 71px; top: 189px; width: 560px; list-style: none;
    font-size: 12px; line-height: 13.5px; color: var(--ink-soft);
  }
  .points > li { position: relative; padding-left: 8px; width: 480px; margin-bottom: 11px; }
  .points > li:first-child { width: 640px; margin-bottom: 18px; }
  .points > li::before { content: "•"; position: absolute; left: 0; color: var(--brand-blue); }
  .points .lead { font-size: 14px; font-weight: 700; color: var(--ink); line-height: 18px; white-space: nowrap; }
  .points ul { list-style: none; margin: 3px 0 0 30px; }
  .points ul li { position: relative; padding-left: 8px; white-space: nowrap; }
  .points ul li::before { content: "•"; position: absolute; left: 0; color: var(--brand-blue); }
</style>
</head>
<body>

<section class="slide slide--title">
  <svg class="slide-shapes" width="879" height="493" viewBox="0 0 879 493">
    <defs>
      <linearGradient id="photo-tone" x1="0" y1="0" x2="0" y2="1">
        <stop offset="0" stop-color="#7c8aa6"/>
        <stop offset="0.45" stop-color="#8f96a6"/>
        <stop offset="0.55" stop-color="#4b5260"/>
        <stop offset="1" stop-color="#2d3340"/>
      </linearGradient>
    </defs>
    <g class="photo-area" role="img" aria-label="Photograph of a city skyline across a river with two moored sailboats">
      <polygon points="431,0 879,0 879,493 275,493" fill="url(#photo-tone)"/>
    </g>
    <polygon class="accent-strip" points="0,0 88,0 0,364" fill="var(--brand-blue)"/>
    <polygon class="url-slash" points="242,438 251,438 265,465 256,465" fill="var(--strip-grey)"/>
  </svg>

  <div class="brand">
    <span class="brand-dot"></span>
    <span class="brand-name">Pinebrook Capital</span>
  </div>

  <h1 class="deck-title">Introduction to<br>Non-Control Capital</h1>
  <p class="deck-subtitle">The Lower Middle Market Private Company Strategy for Raising Capital While <strong>Maintaining Business Control</strong></p>

  <div class="url-bar">www.<strong>pinebrookcapital</strong>.com</div>
</section>

<section class="slide slide--content">
  <svg class="slide-shapes" width="879" height="493" viewBox="0 0 879 493">
    <defs>
      <linearGradient id="faint-photo" x1="0" y1="0" x2="0" y2="1">
        <stop offset="0" stop-color="#ffffff"/>
        <stop offset="0.5" stop-color="#eeeeee"/>
        <stop offset="1" stop-color="#e2e2e2"/>
      </linearGradient>
      <linearGradient id="chevron-blue" x1="0" y1="0" x2="1" y2="1">
        <stop offset="0" stop-color="var(--brand-blue)"/>
        <stop offset="0.5" stop-color="var(--brand-blue-light)"/>
        <stop offset="1" stop-color="var(--brand-blue)"/>
      </linearGradient>
    </defs>
    <rect class="photo-area" width="879" height="493" fill="url(#faint-photo)" role="img" aria-label="Faded photograph of a city skyline and sailboats on a river"/>
    <polygon class="side-strip" points="0,0 88,0 0,358" fill="var(--strip-grey)"/>
    <polygon class="side-chevron" points="766,0 879,0 879,493 763,493 842,242" fill="url(#chevron-blue)"/>
    <polygon class="url-slash" points="277,452 286,452 300,479 291,479" fill="var(--strip-grey)"/>
  </svg>

  <div class="brand">
    <span class="brand-dot"></span>
    <span class="brand-name">Pinebrook Capital</span>
  </div>

  <h2 class="section-heading">Introduction:</h2>
  <span class="section-rule"></span>

  <ul class="points">
    <li><span class="lead">Private company owners have traditionally considered two capital raising options:</span>
      <ul>
        <li>Borrow from a local bank, or</li>
        <li>Sell most or all of the company to a change-of-control investor (aka Buyout firm)</li>
      </ul>
    </li>
    <li>An alternative most have not considered is the raising of Non-Control Capital, or capital that is invested into the business yet allows those same owners to retain controlling interest in their company</li>
    <li>Non-Control Capital is not appropriate for every private company owner but neither is a Change-of-Control sale</li>
    <li>The key is to determine what the business and owners require, and then partner with an investor best aligned with those needs so that long-term company growth, and personal goals, can both be achieved</li>
  </ul>

  <div class="url-bar">www.<strong>pinebrookcapital</strong>.com</div>
</section>

</body>
</html>
```